Renewed Website Design for B2B Company

We need a renewed design for Van Roost - an international trading company in raw materials: natural oils (essential oils, fatty oils, and extracts) and related products such as aromas, fragrances, etc.

Page designs to create:

1. Home page (see the mockup, the content and structure should be exactly like this, however feel free creative-wise)

2. Products page(includes all the 11 product categories which you see on van-roost.nl and some small description of them).

Current website: van-roost.nl
Competitors' websites: brivelmaroilworks.com & qtuvx.com (they don't have particularly perfect websites design-wise, however, it's mostly to give you the idea of this market).

Please, go to this Google Drive folder - https://kortlink.example/7TxwPq - to see Van Roost's logo in different variations, brandbook with colors, fonts, and a brochure with 'mood board' pictures.

Target Market(s)

B2B companies needing white label products like natural/essential/fatty oils, fragrances etc.

Number of Pages Required

2 page

Font styles to use
Other font styles liked:
• Open Sans

Colors

Designer to choose colors to be used in the design.

Requirements
Should not have
• No images with people; no turqoise, blue or pink colors; no overlays over pictures

```html
<!DOCTYPE html>
<html lang="nl">
<head>
<meta charset="utf-8">
<title>Van Roost – Uw betrouwbare sourcingpartner</title>
<link href="https://fonts.googleapis.com/css2?family=Open+Sans:wght@400;600;700&family=Exo+2:wght@300;400&display=swap" rel="stylesheet">
<style>
:root{
  --green:#1a8a68;
  --red:#c8102e;
  --ink:#222;
  --line:#7cbfa9;
  --mint:#def6f0;
  --footer:#1e1f23;
  --white:#fff;
}
*{margin:0;padding:0;box-sizing:border-box}
html,body{width:1200px;height:4706px;overflow:hidden}
body{position:relative;font-family:"Open Sans",Arial,sans-serif;color:var(--ink);background:var(--white)}
.abs{position:absolute}
a{color:inherit;text-decoration:none}

/* header */
.site-nav{position:absolute;top:0;left:0;width:1200px;height:84px;z-index:5;font-size:17px;font-weight:600;color:#222}
.nav-item{position:absolute;top:42px}
.nav-item.active{top:0;left:99px;width:69px;height:84px;background:var(--green);color:#fff;text-align:center;line-height:104px}
.caret{font-size:11px;color:var(--green);margin-left:4px}
.wordmark{position:absolute;left:510px;top:38px;font-size:24px;font-weight:600;color:var(--ink);letter-spacing:.5px;white-space:nowrap}
.lang{position:absolute;left:846px;top:36px;width:86px;height:38px;border-radius:19px;background:var(--green);color:#fff;font-size:14px;font-weight:400;display:flex;align-items:center;gap:8px;padding-left:6px}
.flag{width:28px;height:28px;border-radius:50%;background:linear-gradient(#c8102e 0 33%,#fff 33% 66%,#21468b 66%);border:2px solid #fff}
.search{position:absolute;left:941px;top:36px;width:162px;height:38px;border-radius:19px;background:#fff;box-shadow:0 0 0 1px #ddd;font-size:12px;font-weight:400;color:#555;padding:10px 18px}
.search svg{position:absolute;right:14px;top:13px}

/* hero */
.hero{position:absolute;top:0;left:0;width:1200px;height:700px}
.hero-photo{position:absolute;inset:0;background:
  radial-gradient(ellipse at 82% 35%,#a8511c 0,#7b3615 18%,transparent 40%),
  radial-gradient(ellipse at 62% 30%,#e08a2c 0,transparent 28%),
  radial-gradient(ellipse at 95% 60%,#4a6b2a 0,transparent 25%),
  linear-gradient(100deg,#ece5da 0%,#ddd2c2 40%,#c79a6a 70%,#6e4a2e 100%)}
.hero-welcome{position:absolute;left:104px;top:222px;font-size:21px;font-weight:600;color:var(--green)}
.hero-title{position:absolute;left:99px;top:246px;font-family:"Exo 2",sans-serif;font-weight:300;font-size:84px;letter-spacing:2px;color:var(--green);line-height:1}
.hero-sub{position:absolute;left:103px;top:338px;font-size:32px;color:var(--red);font-weight:400}
.btn{position:absolute;display:flex;align-items:center;justify-content:center;background:var(--red);color:#fff;font-size:17px;font-weight:600;border-radius:6px}
.hero .btn{left:113px;top:402px;width:139px;height:44px;font-size:20px;font-weight:400}

/* section titles */
.section-title{position:absolute;font-size:30px;font-weight:600;color:var(--green);letter-spacing:1px}
.section-title::after{content:"";position:absolute;left:6px;right:-2px;bottom:2px;height:6px;background:var(--red);z-index:-1}

/* product rows */
.drop{position:absolute;width:362px;height:424px}
.row-title{position:absolute;font-size:35px;font-weight:400;color:#1a1a1a}
.row-text{position:absolute;width:510px;font-size:18px;line-height:29px;color:#222}
.row-rule{position:absolute;width:478px;height:2px;background:var(--line)}
.row .btn{width:141px;height:44px}

/* about band */
.about-band{position:absolute;left:0;top:2740px;width:1200px;height:570px}
.about-photo{position:absolute}
.about-title{position:absolute;left:659px;top:2880px;font-size:33px;font-weight:600;color:#fff}
.about-title::after{content:"";position:absolute;left:4px;right:0;bottom:4px;height:6px;background:var(--red);z-index:-1}
.about-text{position:absolute;left:662px;top:2957px;width:450px;font-size:17px;line-height:30px;color:#fff}

/* method */
.method-title{position:absolute;left:99px;top:3418px;font-size:35px;font-weight:600;color:#1a1a1a}
.method-title::after{content:"";position:absolute;left:2px;right:0;bottom:4px;height:7px;background:var(--red);z-index:-1}
.method-text{position:absolute;left:99px;top:3512px;width:500px;font-size:17.5px;line-height:30.3px;text-align:justify;color:#222}

/* story */
.story{position:absolute;left:0;top:3943px;width:1200px;height:457px;background:var(--mint)}
.story-title{position:absolute;left:0;top:4020px;width:1200px;text-align:center;font-size:36px;font-weight:400;color:#1a1a1a}
.story-text{position:absolute;left:200px;top:4087px;width:800px;text-align:center;font-size:21px;line-height:30px;color:#1a1a1a}
.herb-strip{position:absolute;left:0;width:1200px;height:175px;background:
  linear-gradient(180deg,rgba(222,246,240,0) 0%,#6c8a4a 35%,#3e5a2a 70%,#2a2a20 100%)}

/* footer */
.footer{position:absolute;left:0;top:4400px;width:1200px;height:306px;background:var(--footer);color:#fff}
.footer-address{position:absolute;left:99px;top:24px;font-size:15.5px;line-height:26px;display:flex;gap:10px}
.footer .wordmark{left:496px;top:54px;color:#fff}
.footer-phone{position:absolute;left:860px;top:60px;font-size:19px;display:flex;align-items:center;gap:10px}
.footer-nav{position:absolute;top:144px;left:0;width:1200px;font-size:16px;font-weight:600}
.footer-nav a{position:absolute;top:0}
.footer-rule{position:absolute;left:99px;top:213px;width:1003px;height:1px;background:#555}
.copyright{position:absolute;left:99px;top:236px;font-size:15px}
.social{position:absolute;left:853px;top:236px;font-size:15px;display:flex;align-items:center;gap:14px}
.social i{display:block;width:16px;height:16px;border-radius:50%;background:#fff}
</style>
</head>
<body>

<header class="site-nav">
  <a class="nav-item active" href="#">huis</a>
  <a class="nav-item" style="left:184px" href="#">Bedrijf</a>
  <a class="nav-item" style="left:276px" href="#">Producten<span class="caret">&#8964;</span></a>
  <a class="nav-item" style="left:411px" href="#">Vacature</a>
  <div class="wordmark">Van Roost</div>
  <a class="nav-item" style="left:742px" href="#">Contact</a>
  <div class="lang"><span class="flag"></span>- DT</div>
  <div class="search">zoeken
    <svg width="12" height="12" viewBox="0 0 12 12"><circle cx="5" cy="5" r="3.5" fill="none" stroke="#333" stroke-width="1.6"/><line x1="7.5" y1="7.5" x2="11" y2="11" stroke="#333" stroke-width="1.8"/></svg>
  </div>
</header>

<section class="hero">
  <div class="hero-photo" role="img" aria-label="Flesje etherische olie met gedroogde sinaasappel, steranijs en kaneel op houten tafel"></div>
  <svg class="abs" style="left:0;top:0" width="1200" height="700" viewBox="0 0 1200 700">
    <path d="M0 575 C320 700 760 700 1200 598 L1200 700 L0 700Z" fill="#fff"/>
    <path d="M0 575 C320 700 760 700 1200 598" fill="none" stroke="var(--green)" stroke-width="6"/>
  </svg>
  <p class="hero-welcome">welkom bij</p>
  <h1 class="hero-title">VAN ROOST</h1>
  <p class="hero-sub">Uw betrouwbare sourcingpartner</p>
  <a class="btn" href="#">Begin</a>
</section>

<h2 class="section-title" style="left:510px;top:768px">PRODUCTEN</h2>

<svg width="0" height="0" style="position:absolute">
  <defs>
    <linearGradient id="g-oil" x1="0" y1="0" x2="1" y2="1"><stop offset="0" stop-color="#4b3a22"/><stop offset=".5" stop-color="#8a5a2a"/><stop offset="1" stop-color="#b44a8a"/></linearGradient>
    <linearGradient id="g-perfume" x1="0" y1="0" x2="0" y2="1"><stop offset="0" stop-color="#3a3a9a"/><stop offset=".6" stop-color="#8a86d0"/><stop offset="1" stop-color="#3b2e7a"/></linearGradient>
    <linearGradient id="g-raw" x1="0" y1="0" x2="0" y2="1"><stop offset="0" stop-color="#6b8a3a"/><stop offset=".6" stop-color="#c8a040"/><stop offset="1" stop-color="#4a3520"/></linearGradient>
    <linearGradient id="g-body" x1="0" y1="0" x2="1" y2="0"><stop offset="0" stop-color="#9ab870"/><stop offset=".55" stop-color="#3a2a1a"/><stop offset="1" stop-color="#8a3a3a"/></linearGradient>
  </defs>
</svg>

<section class="row">
  <svg class="drop" style="left:159px;top:840px" viewBox="0 0 200 234" role="img" aria-label="Flesjes natuurlijke olie met bloemen"><path d="M100 0 C130 40 200 88 200 134 A100 100 0 0 1 0 134 C0 88 70 40 100 0Z" fill="url(#g-oil)"/></svg>
  <h3 class="row-title" style="left:589px;top:888px">Natuurlijk oliën</h3>
  <p class="row-text" style="left:591px;top:962px">Keuze uit een uitgebreid assortiment uit voorraad leverbare etherische en vette oliën. Niet op voorraad? Geen probleem! Door onze ruime ervaring en wereldwijde netwerk is nauwelijks een natuurlijke olie die wij niet kunnen leveren.</p>
  <div class="row-rule" style="left:594px;top:1110px"></div>
  <a class="btn" style="left:592px;top:1149px" href="#">Leer meer</a>
</section>

<section class="row">
  <h3 class="row-title" style="left:111px;top:1370px">Parfums en Aroma’s</h3>
  <p class="row-text" style="left:109px;top:1444px">Geur- en smaakstoffen onder de merknaam Aromelle. Onze specialisten ontwikkelen eigen parfum compounds en flavour compounds voor elke toepassing. De mogelijkheden zijn eindeloos.</p>
  <div class="row-rule" style="left:112px;top:1592px"></div>
  <a class="btn" style="left:110px;top:1630px" href="#">Leer meer</a>
  <svg class="drop" style="left:681px;top:1303px" viewBox="0 0 200 234" role="img" aria-label="Parfumflesje tussen paarse bloemen"><path d="M100 0 C130 40 200 88 200 134 A100 100 0 0 1 0 134 C0 88 70 40 100 0Z" fill="url(#g-perfume)"/></svg>
</section>

<section class="row">
  <svg class="drop" style="left:159px;top:1774px" viewBox="0 0 200 234" role="img" aria-label="Vijzel met kruiden en flesjes olie"><path d="M100 0 C130 40 200 88 200 134 A100 100 0 0 1 0 134 C0 88 70 40 100 0Z" fill="url(#g-raw)"/></svg>
  <h3 class="row-title" style="left:590px;top:1840px">Grondstoffen</h3>
  <p class="row-text" style="left:591px;top:1914px">Ingrediënten en halffabricaten die afgeleid zijn van of veel gebruikt worden met natuurlijke oliën. Voor veel producerende bedrijven zijn wij daarmee een one-stop-shop partner.</p>
  <div class="row-rule" style="left:594px;top:2062px"></div>
  <a class="btn" style="left:592px;top:2100px" href="#">Leer meer</a>
</section>

<section class="row">
  <h3 class="row-title" style="left:106px;top:2315px">Bodytekst HP</h3>
  <p class="row-text" style="left:109px;top:2389px">Van Roost is een solide en betrouwbare leverancier van grondstoffen voor de cosmetische-, chemische, reform-, feed- en foodsector. Wij onderscheiden ons door een hoog serviceniveau en uitgebreid aanbod.</p>
  <div class="row-rule" style="left:112px;top:2537px"></div>
  <a class="btn" style="left:110px;top:2574px" href="#">Leer meer</a>
  <svg class="drop" style="left:681px;top:2247px" viewBox="0 0 200 234" role="img" aria-label="Flesje olie met witte jasmijnbloemen"><path d="M100 0 C130 40 200 88 200 134 A100 100 0 0 1 0 134 C0 88 70 40 100 0Z" fill="url(#g-body)"/></svg>
</section>

<section>
  <svg class="about-band" viewBox="0 0 1200 570">
    <path d="M0 80 C250 0 800 10 1200 65 L1200 490 C820 560 420 570 0 480Z" fill="var(--green)"/>
    <path d="M0 480 C420 570 820 560 1200 490" fill="none" stroke="var(--red)" stroke-width="6"/>
  </svg>
  <div class="about-photo" style="left:121px;top:2722px;width:230px;height:311px;background:linear-gradient(160deg,#f2a63a,#c07a2a 50%,#5a3a1e)" role="img" aria-label="Sinaasappel en flesje olie"></div>
  <div class="about-photo" style="left:121px;top:3062px;width:230px;height:238px;background:linear-gradient(160deg,#f6efe6,#d8883a 60%,#8a4a1e)" role="img" aria-label="Flesjes olie met hars"></div>
  <div class="about-photo" style="left:373px;top:2872px;width:228px;height:311px;background:linear-gradient(180deg,#e8eef0,#b8c4c8 40%,#9a4a1a 75%,#3a3a3a)" role="img" aria-label="Apothekersfles met olie en stenen"></div>
  <h2 class="about-title">Over ons</h2>
  <p class="about-text">Dit zijn wij, een groeiend familiebedrijf in Berkel (Hoeven) dat werkt met een professioneel en hecht team &lt;link en beeld&gt;. Wij vinden het van groot belang dat onze klanten tevreden zijn, daarom proberen wij altijd net dat stapje extra te zetten.</p>
  <a class="btn" style="left:669px;top:3137px;width:137px;height:44px" href="#">Leer meer</a>
</section>

<section>
  <h2 class="method-title">Werkwijze</h2>
  <p class="method-text">Wij leveren grondstoffen uit voorraad , standaard verpakt in IBC’s, vaten of jerrycans, maar ook levering in kleinere verpakkingen zijn bij ons mogelijk. De producten worden (zo dicht mogelijk) bij de bron aangekocht of zelf ontwikkeld. Hierdoor en dankzij ons eigen kwaliteitssysteem is de juiste kwaliteit gegarandeerd. Door de directe lijnen zijn wij in staat tot snelle en flexibele levering tegen scherpe prijzen. Hebben we een product niet in ons assortiment dan gaan we op zoek en vinden we een passende oplossing.</p>
  <a class="btn" style="left:102px;top:3817px;width:139px;height:44px" href="#">Leer meer</a>
  <svg class="abs" style="left:670px;top:3400px" width="460" height="470" viewBox="0 0 460 470">
    <defs><linearGradient id="g-method" x1="0" y1="0" x2="1" y2="1"><stop offset="0" stop-color="#c9b8d8"/><stop offset=".45" stop-color="#8a4a1a"/><stop offset="1" stop-color="#4a2e1e"/></linearGradient></defs>
    <circle cx="236" cy="240" r="222" fill="var(--red)"/>
    <circle cx="229" cy="229" r="221" fill="#fff"/>
    <circle cx="229" cy="229" r="218" fill="url(#g-method)" role="img" aria-label="Druppelflesjes olie met lavendel"/>
  </svg>
</section>

<section class="story">
  <div class="herb-strip" style="top:282px" role="img" aria-label="Rij kruiden, lavendel en flesjes olie"></div>
</section>
<h2 class="story-title">Verhaal Van Roost</h2>
<p class="story-text">Van Roost (anno 1979) bestaat ruim 40 jaar. Wil je meer weten over het verhaal achter Van Roost? Klik dan hier &lt;klik&gt;.</p>
<a class="btn" style="left:532px;top:4177px;width:138px;height:44px" href="#">Leer meer</a>

<footer class="footer">
  <div class="footer-address">
    <svg width="12" height="16" viewBox="0 0 12 16" style="margin-top:5px"><path d="M6 0a6 6 0 0 1 6 6c0 4-6 10-6 10S0 10 0 6a6 6 0 0 1 6-6z" fill="#fff"/><circle cx="6" cy="6" r="2.2" fill="var(--footer)"/></svg>
    <span>Molenkamp 8, 5942 KR Berkel:<br>Berkel (Hoeven 4410) – The Netherlands</span>
  </div>
  <div class="wordmark">Van Roost</div>
  <div class="footer-phone">
    <svg width="16" height="16" viewBox="0 0 16 16"><path d="M3 1l3 3-2 2c1 2 3 4 5 5l2-2 3 3-2 3C6 15 1 10 0 3z" fill="#fff"/></svg>
    +31 (0)40-2741836
  </div>
  <nav class="footer-nav">
    <a style="left:310px" href="#">HUIS</a>
    <a style="left:404px" href="#">BEDRIJF</a>
    <a style="left:519px" href="#">PRODUCTEN</a>
    <a style="left:674px" href="#">VACATURE</a>
    <a style="left:813px" href="#">CONTACT</a>
  </nav>
  <div class="footer-rule"></div>
  <p class="copyright">© copyrights 2022 van-roost | All Rights Reserved</p>
  <div class="social">Sociale media: <i></i><i></i><i></i><i></i></div>
</footer>

</body>
</html>
```